Business Card Design Project

We need a business card for a new technology services company. We develop software and implement software packages for our business customers and although we will begin with just one or two service offerings, our service offerings will expand over time. Our name comes from the an author, KL Barrow, and his "idea" was that opportunity should be based on ability and achievement, not on social status.

We would like to see a design that is standard in its size and shape, but stands apart in its dramatic color contrasts. The card should not use too many colors - the colors used in the background should highlight the brilliant blues of the logo (see attachment) to dramatic effect. The background should not be white.

If necessary, you can change the color of the words "KL Barrow", but not the word "Idea".

Card size should be U.S. standard 2 inches by 3.5 inches and provide for 1/8 inch bleed area on each side.

We need a design for both sides of the business card, one side communicating the company logo and contact information, the other side being purely graphical, incorporating the logo but no other information.

Contact Information Required:
Kate Brook
KateBrook@klbarrowvista.com
614-387-2259

Target Market(s)

Business executives

Industry/Entity Type

Software

Requirements
Must have
• It must have the full company logo on one side, and at least the graphic element of the logo on the other. Either that or the full logo on both.
Nice to have
• It would be nice to have a design that could work without needing two different textures. For example, it would be nice if the entire card could be shiny, not just parts of the card.

It would also be nice if texture is something we could add later.
Should not have
• The card should not use the color green.

```html
<!DOCTYPE html>
<html lang="en">
<head>
<meta charset="utf-8">
<title>Barrow Vista – Business Card</title>
<link rel="stylesheet" href="https://fonts.googleapis.com/css2?family=Roboto:wght@400;700&display=swap">
<style>
  :root {
    --page-bg: #e9e9ee;
    --card-dark: #1c1c1c;
    --card-mid: #2e2e2e;
    --card-edge: #0f0f0f;
    --brand-blue: #1ea0e0;
    --brand-blue-deep: #0a7fc0;
    --rule-silver: #9a9a9a;
    --text-light: #ffffff;
  }
  * { box-sizing: border-box; margin: 0; padding: 0; }
  html, body {
    width: 1200px;
    height: 987px;
    overflow: hidden;
    background: var(--page-bg);
    font-family: "Roboto", Arial, sans-serif;
  }
  .sheet {
    position: relative;
    width: 1200px;
    height: 987px;
    display: flex;
    align-items: center;
    justify-content: center;
    gap: 48px;
  }
  .card {
    position: relative;
    width: 540px;
    height: 309px;
    border-radius: 26px;
    overflow: hidden;
    background:
      radial-gradient(ellipse at 45% 35%, var(--card-mid) 0%, var(--card-dark) 60%, var(--card-edge) 100%);
    box-shadow: 0 10px 28px rgba(0,0,0,0.18);
  }
  .wordmark {
    position: absolute;
    font-weight: 400;
    color: var(--text-light);
    letter-spacing: 2px;
    text-transform: uppercase;
    white-space: nowrap;
  }
  /* front */
  .card-front .wordmark {
    top: 62px;
    left: 64px;
    font-size: 34px;
  }
  .band {
    position: absolute;
    inset: 0;
    width: 100%;
    height: 100%;
  }
  .contact {
    position: absolute;
    left: 0;
    right: 0;
    top: 196px;
    text-align: center;
    color: var(--text-light);
  }
  .contact .person-name {
    font-weight: 700;
    font-size: 22px;
    letter-spacing: 1px;
    text-transform: uppercase;
  }
  .contact .details {
    margin-top: 14px;
    display: flex;
    justify-content: center;
    gap: 22px;
    font-size: 15px;
    font-weight: 400;
  }
  .contact .detail {
    display: flex;
    align-items: center;
    gap: 6px;
  }
  .contact svg { width: 14px; height: 14px; }
  /* back */
  .card-back .wordmark {
    top: 50%;
    left: 50%;
    transform: translate(-50%, -50%);
    font-size: 40px;
  }
</style>
</head>
<body>
<main class="sheet">

  <section class="card card-front" aria-label="Business card front">
    <svg class="band" viewBox="0 0 540 309" preserveAspectRatio="none" aria-hidden="true">
      <defs>
        <linearGradient id="bandFill" x1="0" y1="0" x2="1" y2="1">
          <stop offset="0" stop-color="#1ea0e0"/>
          <stop offset="1" stop-color="#0a7fc0"/>
        </linearGradient>
      </defs>
      <path d="M0 150 Q 260 150 540 250 L540 309 L0 309 Z" fill="none" stroke="#9a9a9a" stroke-width="3" transform="translate(0,-6)"/>
      <path d="M0 150 Q 260 150 540 250 L540 309 L0 309 Z" fill="url(#bandFill)"/>
    </svg>
    <p class="wordmark">Barrow Vista</p>
    <div class="contact">
      <p class="person-name">Kate Brook</p>
      <div class="details">
        <span class="detail">
          <svg viewBox="0 0 16 16" aria-hidden="true"><circle cx="8" cy="8" r="7" fill="none" stroke="currentColor" stroke-width="1.4"/><path d="M5.5 4.5 L7 6 L6.2 7 Q7 9 9 9.8 L10 9 L11.5 10.5 L10.5 11.5 Q7 11.5 4.5 5.5 Z" fill="currentColor"/></svg>
          614-387-2259
        </span>
        <span class="detail">
          <svg viewBox="0 0 16 16" aria-hidden="true"><rect x="1.5" y="3.5" width="13" height="9" fill="none" stroke="currentColor" stroke-width="1.4"/><path d="M1.5 3.5 L8 9 L14.5 3.5" fill="none" stroke="currentColor" stroke-width="1.4"/></svg>
          KateBrook@klbarrowvista.com
        </span>
      </div>
    </div>
  </section>

  <section class="card card-back" aria-label="Business card back">
    <p class="wordmark">Barrow Vista</p>
  </section>

</main>
</body>
</html>
```